Retail Package for Ammunition Company

We are looking for a packaging design for a retail boxed ammunition. The "look". Attached will be the logo to be used. The logo is attached and a can be manipulated on the box. Box to represent strength and accuracy. Will need to provide .psd files to allow in house personnel to add/remove text to other calibers and warnings. Wow me with your designs!

Browse Other Brands: http://www.brightfalconsupply.com/brands

The packaging needs to include:
Logo- provided and the following text:

FRONT 1. 9mm 115gr FMJ

BACK 2. WARNING: To avoid serious injury: (1) use only ammunition in good condition; use only in modern firearms in good condition marked for .22 Long Rifle (LR) cartridges; (2) always be sure barrel is free of any obstructions; the barrel should be checked in case of light recoil, or an unusually loud or weak sound heard during firing; (3) wear eye and ear protection; (4) if gun fails to fire, avoid exposure to breech when unloading and point muzzle in a safe direction. Keep firearm pointed in safe direction at all times; (5) discharge may occur if rim is struck; handle with caution, do not drop. (6) Do not shoot at hard surfaces or water to prevent ricochet; (7) Bullet is capable of traveling extreme distances. Know your backstop; (8) Store in cool dry place

3. LEAD WARNING: Discharging firearms in poorly ventilated areas, cleaning firearms, or handling ammunition may result in exposure to lead and other substances known to cause birth defects, reproductive harm, and other serious physical injury. Have adequate ventilation at all times. Wash hands thoroughly after exposure.

Dimensions ; (LxWxH): 5.25" x 2.625" x 1.125"

Target Market(s)

Ammunition Industry

```html
<!DOCTYPE html>
<html lang="en">
<head>
<meta charset="utf-8">
<title>Stone Kestrel Armory – 9mm Retail Box</title>
<link rel="stylesheet" href="https://fonts.googleapis.com/css2?family=Cinzel:wght@700&family=Russo+One&family=Nunito+Sans:ital,wght@1,400;1,800&display=swap">
<style>
  :root{
    --page-bg:#dfeaf7;
    --cyan:#12c8f2;
    --blue:#1238e0;
    --navy:#04125a;
    --red:#a80000;
    --red-bright:#d80010;
    --black:#000;
    --white:#fff;
  }
  *{margin:0;padding:0;box-sizing:border-box}
  html,body{width:1200px;height:1200px;overflow:hidden}
  body{background:linear-gradient(180deg,#6ea6ea 0%,var(--page-bg) 100%);position:relative;font-family:"Nunito Sans",sans-serif}

  .panel{position:absolute;overflow:hidden}

  /* Top face */
  .top-face{left:206px;top:190px;width:788px;height:394px;
    background:linear-gradient(160deg,var(--cyan) 0%,#1a8ff0 35%,var(--blue) 70%,#2a2cc0 100%)}
  .top-face__texture{position:absolute;inset:0;
    background:radial-gradient(ellipse at 75% 10%,rgba(255,255,255,.25),transparent 45%),
               linear-gradient(175deg,transparent 55%,rgba(4,18,90,.55) 56%,var(--navy) 100%)}
  .top-face__mark{position:absolute;left:50px;top:200px;display:flex;align-items:center;gap:16px}
  .mark-dot{width:64px;height:64px;border-radius:50%;background:var(--red-bright)}
  .mark-name{font-family:"Cinzel",serif;font-weight:700;font-size:40px;line-height:1.05;color:var(--red-bright)}
  .top-face__brand{position:absolute;right:60px;top:40px;display:flex;align-items:center;gap:10px;
    font-family:"Cinzel",serif;font-weight:700;font-size:22px;color:var(--white)}
  .brand-dot{width:18px;height:18px;border-radius:50%;background:var(--white)}
  .top-face__caliber{position:absolute;right:60px;top:105px;
    font-family:"Russo One",sans-serif;font-size:40px;color:var(--white);letter-spacing:2px;white-space:nowrap}

  /* Front face */
  .front-face{left:206px;top:584px;width:788px;height:169px;background:var(--red)}
  .lead-warning{position:absolute;left:210px;top:16px;width:556px;height:137px;
    background:var(--black);border-radius:34px;padding:16px 26px;
    color:var(--red-bright);font-style:italic;font-size:13px;line-height:1.4;text-align:center;
    display:flex;align-items:center}
  .lead-warning strong{font-weight:800;font-size:15px}

  /* End face */
  .end-face{left:403px;top:790px;width:394px;height:169px;background:var(--red);
    display:flex;align-items:center;justify-content:center;gap:14px}
  .end-face .brand-dot{width:30px;height:30px}
  .end-face__name{font-family:"Cinzel",serif;font-weight:700;font-size:30px;color:var(--white);line-height:1.05}
</style>
</head>
<body>
  <section class="panel top-face">
    <div class="top-face__texture" role="img" aria-label="Abstract blue light-streak background"></div>
    <div class="top-face__brand"><span class="brand-dot"></span>STONE KESTREL ARMORY</div>
    <div class="top-face__caliber">1. 9mm 115gr FMJ</div>
    <div class="top-face__mark">
      <span class="mark-dot"></span>
      <span class="mark-name">STONE KESTREL<br>ARMORY</span>
    </div>
  </section>

  <section class="panel front-face">
    <p class="lead-warning"><span><strong>LEAD WARNING:</strong> Discharging firearms in poorly ventilated areas, cleaning firearms, or handling ammunition may result in exposure to lead and other substances known to cause birth defects, reproductive harm, and other serious physical injury. Have adequate ventilation at all times. Wash hands thoroughly after exposure.</span></p>
  </section>

  <section class="panel end-face">
    <span class="brand-dot"></span>
    <span class="end-face__name">STONE KESTREL<br>ARMORY</span>
  </section>
</body>
</html>
```